BOLD PINE HEATING AND COOLING

Industry/Entity Type

Hvac

Requirements
Must have
• logo
My name: Gavin Pruszynski
Phone number 555-309-4461
Text:
Furnace and AC repairs
New furnace and AC installation
Ductwork
Gas lines
Water Tanks
Tankless water heaters
Nice to have
• Profesional modern look

```html
<!DOCTYPE html>
<html lang="en">
<head>
<meta charset="utf-8">
<title>Bold Pine Heating and Cooling – Business Card</title>
<link rel="stylesheet" href="https://fonts.googleapis.com/css2?family=Montserrat:wght@400;500&family=Oswald:wght@500&display=swap">
<style>
  :root {
    --page: #161616;
    --card: #262626;
    --card-edge: #2e2e2e;
    --silver: #a9a9a9;
    --white: #f2f2f2;
    --blue: #1f63c4;
    --green: #6cbd45;
  }
  * { box-sizing: border-box; margin: 0; padding: 0; }
  html, body { width: 1200px; height: 900px; overflow: hidden; background: var(--page); }
  body { font-family: "Montserrat", sans-serif; color: var(--white); }
  .canvas { position: relative; width: 1200px; height: 900px; }
  .card {
    position: absolute; left: 250px; width: 700px; height: 400px;
    background: linear-gradient(160deg, var(--card-edge), var(--card) 60%);
    box-shadow: 0 14px 30px rgba(0,0,0,.6);
  }
  .card--back { top: 35px; }
  .card--front { top: 465px; }

  .wordmark { display: flex; align-items: center; gap: 14px; font-weight: 500; letter-spacing: 3px; text-transform: uppercase; }
  .wordmark__mark { width: 34px; height: 34px; }
  .wordmark__text { line-height: 1.25; }
  .wordmark__name { display: block; font-size: 34px; }
  .wordmark__sub { display: block; font-size: 14px; letter-spacing: 2.5px; }

  .card--back .wordmark { position: absolute; top: 110px; left: 50%; transform: translateX(-50%); color: var(--silver); }
  .card--back .wordmark__mark { background: var(--silver); }
  .services { position: absolute; top: 262px; left: 0; right: 0; text-align: center; font-size: 16px; line-height: 1.7; letter-spacing: .5px; }
  .services .sep { color: var(--green); padding: 0 6px; }

  .card--front .wordmark { position: absolute; top: 80px; left: 50%; transform: translateX(-50%); color: var(--blue); }
  .card--front .wordmark__mark { background: var(--blue); }
  .person { position: absolute; top: 245px; left: 60px; width: 230px; text-align: right; }
  .person__name { font-family: "Oswald", sans-serif; font-weight: 500; font-size: 34px; color: var(--blue); text-transform: uppercase; letter-spacing: -.5px; line-height: 1.1; }
  .person__role { font-size: 18px; margin-top: 6px; }
  .divider { position: absolute; top: 240px; left: 318px; width: 2px; height: 86px; background: var(--green); }
  .contacts { position: absolute; top: 240px; left: 350px; list-style: none; font-size: 18px; line-height: 30px; }
  .contacts li { display: flex; align-items: center; gap: 12px; }
  .contacts svg { width: 15px; height: 15px; fill: none; stroke: var(--green); stroke-width: 1.6; }
</style>
</head>
<body>
<main class="canvas">

  <section class="card card--back">
    <div class="wordmark">
      <span class="wordmark__mark"></span>
      <span class="wordmark__text">
        <span class="wordmark__name">Bold Pine</span>
        <span class="wordmark__sub">Heating and Cooling</span>
      </span>
    </div>
    <p class="services">
      Furnace and AC repairs<span class="sep">|</span>New furnace and AC installation<br>
      Ductwork<span class="sep">|</span>Gas lines<span class="sep">|</span>Water Tanks<span class="sep">|</span>Tankless water heaters
    </p>
  </section>

  <section class="card card--front">
    <div class="wordmark">
      <span class="wordmark__mark"></span>
      <span class="wordmark__text">
        <span class="wordmark__name">Bold Pine</span>
        <span class="wordmark__sub">Heating and Cooling</span>
      </span>
    </div>
    <div class="person">
      <p class="person__name">Gavin Pruszynski</p>
      <p class="person__role">Director</p>
    </div>
    <span class="divider"></span>
    <ul class="contacts">
      <li><svg viewBox="0 0 16 16"><path d="M4 1.5l2.5 3-1.5 1.5c.8 2 2.5 3.7 4.5 4.5l1.5-1.5 3 2.5-1.5 2.5C7.5 13.5 2.5 8.5 1.5 3z"/></svg>555-309-4461</li>
      <li><svg viewBox="0 0 16 16"><rect x="1.5" y="3.5" width="13" height="9"/><path d="M1.5 3.5l6.5 5 6.5-5"/></svg>info@boldpineheating.com</li>
      <li><svg viewBox="0 0 16 16"><circle cx="8" cy="8" r="6.5"/><ellipse cx="8" cy="8" rx="3" ry="6.5"/><path d="M1.5 8h13"/></svg>www.boldpineheating.com</li>
    </ul>
  </section>

</main>
</body>
</html>
```